Exec Conference Design Concept

We need to refresh & update nonprofit association graphic design for annual meeting. The graphics will be used to promote the event primarily through digital communications & social media. Other materials we generate for this event are the agenda & billboard content. You can view the existing design at www.lutavorin.org under Events.

The target audience is primarily male, ages 35-60 in executive positions in C-Corps. The conference topics center on manufacturing regulations, marketing trends, and the economy. This conference has been around almost 30 years so we need something to invigorate potential registrants that will get their attention. It still needs to be professional and business-like.

In addition to a new design concept we would like to update the color palette. We’ve attached some mood boards with potential color & font suggestions. Our company logo is also attached and is the only design element tied to our branding that cannot be changed.

Designs should be energetic and sophisticated. Ideally, we would like the designs in Adobe Indesign or Photoshop. However, we can work with Illustrator.

Target Market(s)

Male business executives age 35-60.

Industry/Entity Type

Polystyrene manufacturing industry supply chain.

Other font styles liked:
• I usually prefer sans serif

Requirements
Must have
• Focus points to draw attention to higher level informational units. For example, some people will only read the headers and not detailed copy.
Nice to have
• Ways to insert bonus content that don’t over power other content. I like to see a good use of white space to enhance readability.

```html
<!DOCTYPE html>
<html lang="en">
<head>
<meta charset="utf-8">
<title>LTV Expo 2026</title>
<link href="https://fonts.googleapis.com/css2?family=Questrial&display=swap" rel="stylesheet">
<style>
:root{
  --teal:#1f5c5a;
  --gold:#b8900f;
  --sand:#e6e1d7;
  --icon:#d6cdbd;
  --band:#f3f3f3;
  --ink:#2b2b2b;
  --white:#ffffff;
}
*{margin:0;padding:0;box-sizing:border-box}
html,body{width:1200px;height:3177px;overflow:hidden;background:var(--white)}
body{position:relative;font-family:"Questrial",Arial,sans-serif;color:var(--ink)}
.abs{position:absolute}
.expo-badge{left:850px;top:42px;width:287px;height:250px;background:var(--sand);border-radius:40px 0 0 0;display:flex;align-items:center;justify-content:center;color:var(--teal);font-size:60px;letter-spacing:1px}
.hero-photo{left:450px;top:368px;width:750px;height:432px;border-radius:170px 0 0 170px/50% 0 0 50%;background:linear-gradient(180deg,#8fb6db 0%,#cfe0ef 45%,#9aa6b0 70%,#dcdfe2 100%)}
.hero-circle{left:-69px;top:242px;width:648px;height:648px;border-radius:50%;background:var(--teal)}
.alliance{left:57px;top:339px;display:flex;align-items:center;gap:18px;color:var(--white);font-size:30px}
.alliance-dot{width:120px;height:120px;border-radius:50%;background:var(--gold)}
.hero-title{left:55px;top:480px;color:var(--white);font-size:80px;line-height:94px;letter-spacing:3px;font-weight:400}
.hero-tag{left:56px;top:680px;color:var(--white);font-size:24px;line-height:37px}
.topic-band{left:0;top:1182px;width:1200px;height:477px;background:var(--band)}
.topic{width:394px;text-align:center}
.topic-photo{width:294px;height:294px;border-radius:50%;margin:0 auto}
.topic h2{font-weight:400;font-size:36px;margin-top:30px;color:var(--ink)}
.topic p{font-size:23px;line-height:37px;margin-top:22px;color:#3a3a3a}
.register{left:438px;top:1614px;width:324px;height:99px;border-radius:50px;background:var(--teal);color:var(--white);font-size:30px;display:flex;align-items:center;justify-content:center}
.info-row{left:0;top:1852px;width:1200px;height:206px}
.divider{top:0;width:3px;height:206px;background:#ece8e0}
.info{top:20px;width:400px;text-align:center}
.info svg{display:block;margin:0 auto;height:50px}
.info h3{font-weight:400;font-size:28px;margin-top:18px}
.info p{font-size:23px;margin-top:22px}
.attend-band{left:0;top:2275px;width:1200px;height:392px;background:var(--teal)}
.attend-text{left:100px;top:2370px;width:400px;text-align:center;color:var(--white)}
.attend-text h2{font-weight:400;font-size:37px}
.attend-text p{font-size:23px;line-height:38px;margin-top:22px}
.attend-photo{left:540px;top:2177px;width:606px;height:606px;border-radius:50%;background:radial-gradient(circle at 60% 40%,#6f8aa6 0%,#2c3e55 60%,#1b2838 100%)}
.social{left:490px;top:2836px;display:flex;gap:12px}
.social span{width:46px;height:46px;border-radius:50%;background:var(--teal)}
.site{left:0;top:2906px;width:1200px;text-align:center;font-size:28px;color:#3a3a3a}
.legal{left:0;width:1200px;text-align:center;font-size:23px;color:#333}
.legal a{color:#333}
</style>
</head>
<body>
  <div class="abs expo-badge">LTV Expo</div>

  <div class="abs hero-photo" role="img" aria-label="Industrial plant with steel towers and silos under a bright cloudy sky"></div>
  <div class="abs hero-circle"></div>
  <div class="abs alliance"><span class="alliance-dot"></span><span>Lutavorin Alliance</span></div>
  <h1 class="abs hero-title">LTV EXPO<br>2026</h1>
  <p class="abs hero-tag">Regulatory clarity. Economic insight.<br>Industry leadership.</p>

  <div class="abs topic-band"></div>
  <div class="abs topic" style="left:7px;top:1035px">
    <div class="topic-photo" role="img" aria-label="Executives seated at a meeting table" style="background:radial-gradient(circle at 55% 45%,#6b5a55 0%,#4a2f2b 55%,#2a1c1a 100%)"></div>
    <h2>Regulation</h2>
    <p>Clear guidance on<br>evolving federal and state<br>policy.</p>
  </div>
  <div class="abs topic" style="left:401px;top:1035px">
    <div class="topic-photo" role="img" aria-label="Presenter showing charts on a whiteboard to a colleague" style="background:radial-gradient(circle at 55% 40%,#f1f1ef 0%,#cfcfcb 55%,#8c8a86 100%)"></div>
    <h2>Economics</h2>
    <p>Market trends, forecasts,<br>and financial<br>strategy.</p>
  </div>
  <div class="abs topic" style="left:796px;top:1035px">
    <div class="topic-photo" role="img" aria-label="Smiling businesswoman with colleagues in an office" style="background:radial-gradient(circle at 45% 45%,#d9d6d2 0%,#8a8f99 50%,#1f2a44 100%)"></div>
    <h2>Communications</h2>
    <p>Navigating public<br>perception, advocacy,<br>and messaging.</p>
  </div>

  <div class="abs register">Register Now</div>

  <div class="abs info-row">
    <div class="abs divider" style="left:365px"></div>
    <div class="abs divider" style="left:781px"></div>
    <div class="abs info" style="left:0">
      <svg viewBox="0 0 24 32" aria-hidden="true"><path d="M12 0C5.4 0 0 5.2 0 11.6 0 20 12 32 12 32s12-12 12-20.4C24 5.2 18.6 0 12 0zm0 16a4.5 4.5 0 1 1 0-9 4.5 4.5 0 0 1 0 9z" fill="var(--icon)"/></svg>
      <h3>Location:</h3>
      <p>San Antonio, TX</p>
    </div>
    <div class="abs info" style="left:393px">
      <svg viewBox="0 0 36 32" aria-hidden="true"><rect x="2" y="6" width="32" height="24" rx="2" fill="var(--icon)"/><rect x="8" y="1" width="3" height="8" fill="var(--icon)"/><rect x="25" y="1" width="3" height="8" fill="var(--icon)"/><rect x="6" y="13" width="24" height="2" fill="#fff"/></svg>
      <h3>Dates:</h3>
      <p>August 26-28,2026</p>
    </div>
    <div class="abs info" style="left:773px">
      <svg viewBox="0 0 24 32" aria-hidden="true"><path d="M12 0C5.4 0 0 5.2 0 11.6 0 20 12 32 12 32s12-12 12-20.4C24 5.2 18.6 0 12 0zm0 16a4.5 4.5 0 1 1 0-9 4.5 4.5 0 0 1 0 9z" fill="var(--icon)"/></svg>
      <h3>Office Address :</h3>
      <p>4470 Merrow Blvd, Ste. 310</p>
    </div>
  </div>

  <div class="abs attend-band"></div>
  <div class="abs attend-text">
    <h2>Who Should Attend:</h2>
    <p>LTV manufacturers,<br>regulatory agencies, and<br>industry leaders</p>
  </div>
  <div class="abs attend-photo" role="img" aria-label="Two business leaders in a data center looking at a holographic display"></div>

  <div class="abs social" aria-label="Social channels"><span></span><span></span><span></span><span></span></div>
  <p class="abs site">www.lutavorin.org</p>
  <p class="abs legal" style="top:3000px">You are receiving this email because you subscribed for Lutavorin Alliance event notifications.</p>
  <p class="abs legal" style="top:3056px">If you’d like to stop receiving emails from us, you can <a href="#">unsubscribe here</a>:</p>
</body>
</html>
```